Letterhead Design for Law Firm

**Edit: I have added the photo of a bottom that I like.

------
We are looking for a re-design of our new letterhead. The letterhead is for a law firm and will be used for digital and traditionally printed correspondence.

Here are some suggestions:

- Please use colours are #8ec900 and simple black.
- Please do not use any type of "waves" at the bottom of the page. This is not in style at all.
- Please stay modern yet conservative.
- Please use font Segoe UI Light or similar if you can
- Avoid clipart or illustrations.
- Utilize ample white space in the layout so the design looks clean and information is easy to read at a glance. Don't overcrowd the letterhead.
- Make sure the letterhead design is consistent with our brand identity (see corvelith.ca)
-Please, no black headers or footers.

I am attaching my current letterhead and signature for your convenience.

Remember, the letterhead is an extension of our professional identity. We are a successful firm and trial lawyers who correspond with insurers, judges, lawyers, courts, clients, etc. Make it new, modern, attractive, yet powerful and conservative.

It needs to be easily printable. I would like the bleed removed in print so the black bar the bottom crosses the page (but the text is not near the edges)
Updates

Low design quality

Target Market(s)

Clients, Government Offices, Judiciary, Lawyers, Insurance Companies, Colleagues.

Industry/Entity Type

Law

Other font styles liked:
• Segoe UI LIght, Calibri Light,

Colors
00AB8E
00BBA5
67D7C9
C6EFE9
E9F9F6

Requirements
Must have
• Everything that is on the letterhead now.
Nice to have
• Cutting Edge design, yet conservative.
Should not have
• law firm cliche design, images,

```html
<!DOCTYPE html>
<html lang="en">
<head>
<meta charset="utf-8">
<title>Varenne Personal Injury Lawyers — Letterhead</title>
<link rel="stylesheet" href="https://fonts.googleapis.com/css2?family=Carlito:wght@400;700&family=Open+Sans:wght@400;600;700&display=swap">
<style>
  :root {
    --brand-green: #8bbe21;
    --ink: #111111;
    --paper: #faf8f9;
    --backdrop: #e8e5e1;
  }
  * { margin: 0; padding: 0; box-sizing: border-box; }
  html, body { width: 1200px; height: 1111px; overflow: hidden; background: var(--backdrop); }
  .letterhead {
    position: absolute; left: 185px; top: 20px; width: 830px; height: 1071px;
    background: var(--paper); overflow: hidden;
    box-shadow: 0 4px 14px rgba(0,0,0,0.25);
    color: var(--ink);
    font-family: "Open Sans", "Segoe UI", sans-serif;
  }
  .firm-mark { position: absolute; left: 43px; top: 38px; width: 282px; text-align: center; }
  .firm-name { font-family: "Open Sans", sans-serif; font-weight: 400; font-size: 56px; line-height: 64px; letter-spacing: 1px; color: var(--ink); }
  .firm-tagline { font-family: "Open Sans", sans-serif; font-weight: 400; font-size: 14px; letter-spacing: 1.6px; margin-top: 6px; }

  .contact-block {
    position: absolute; left: 614px; top: 47px; height: 210px;
    border-left: 2px solid var(--brand-green); padding-left: 9px;
    font-size: 11px; line-height: 15.6px;
  }
  .contact-block b { font-weight: 700; }
  .contact-block .web-accent { color: var(--brand-green); font-weight: 700; }
  .contact-block .practice-title { margin-top: 15.6px; font-weight: 700; }

  .letter { position: absolute; left: 58px; font-size: 14px; line-height: 18.6px; }
  .calibri { font-family: "Carlito", "Calibri", sans-serif; }
  .notice { top: 152px; font-size: 15px; }
  .date { top: 189px; }
  .delivery { top: 226px; font-size: 15px; }
  .recipient { top: 264px; font-style: normal; }
  .attention { top: 376px; }
  .salutation { top: 413px; }

  .subject { position: absolute; left: 56px; top: 450px; width: 658px; height: 58px; border-bottom: 1px solid var(--ink); font-size: 15px; line-height: 18.6px; }
  .subject .label { position: absolute; left: 2px; top: 0; }
  .subject .lines { position: absolute; left: 202px; top: 0; white-space: nowrap; }
  .subject sup { font-size: 9px; line-height: 0; vertical-align: 5px; }

  .closing { top: 731px; }
  .closing .firm-caps { font-size: 15px; }
  .signature { position: absolute; left: 58px; top: 783px; width: 192px; height: 42px; background: linear-gradient(90deg, rgba(17,17,17,0.12), rgba(17,17,17,0.04)); }
  .signatory { top: 830px; }
  .signatory .corp { font-size: 12.5px; line-height: 15.6px; }
  .signatory .small { font-size: 11px; line-height: 15.6px; }

  .footer-bar { position: absolute; left: 0; bottom: 0; width: 830px; height: 34px; background: var(--brand-green); }
</style>
</head>
<body>
  <main class="letterhead">
    <div class="firm-mark">
      <div class="firm-name">VARENNE</div>
      <div class="firm-tagline">PERSONAL INJURY LAWYERS</div>
    </div>

    <aside class="contact-block">
      <div>www.<span class="web-accent">CORVELITH</span>.ca</div>
      <div>48 Harbour Lane E., Suite 920</div>
      <div>Brantmere, ON&nbsp; K7R 3B2</div>
      <div><b>T:</b> 555-214-7730</div>
      <div><b>F:</b> 555-214-7731</div>
      <div><b>File Clerk:</b> Marla Quenneville</div>
      <div><b>Email:</b> marla@corvelith.ca</div>
      <div class="practice-title">Practice Restricted</div>
      <div>Serious Personal Injury</div>
      <div>Wrongful Death Litigation</div>
      <div>Long-Term Disability Litigation</div>
      <div>Wrongful Dismissal Litigation</div>
      <div>Employee Terminations</div>
    </aside>

    <p class="letter calibri notice">Without Prejudice</p>
    <p class="letter date">March 13, 2024</p>
    <p class="letter calibri delivery">By Email</p>
    <address class="letter recipient">
      Northvale Insurance Company<br>
      Claims Litigation Department<br>
      62 Fairholm Road North<br>
      P.O. Box 4100<br>
      Elmsbrook, ON&nbsp;&nbsp; P3L 6T8
    </address>
    <p class="letter attention">Attention:&nbsp; Mr. Dorian Whitcombe</p>
    <p class="letter salutation">Mr. Whitcombe:</p>

    <div class="subject calibri">
      <span class="label">Re:</span>
      <div class="lines">
        Halvorsen v. Marchetti et al.<br>
        DOL:&nbsp; September 12, 2019<br>
        Pre-Mediation Settlement Proposal – March 13<sup>th</sup>, 2024
      </div>
    </div>

    <p class="letter closing">Yours very truly,<br><span class="calibri firm-caps">VARENNE PERSONAL INJURY LAWYERS</span></p>
    <div class="signature" role="img" aria-label="Handwritten signature of Owen T. Varenne"></div>
    <div class="letter signatory">
      Owen T. Varenne<br>
      <span class="calibri corp">Varenne Law Professional Corporation</span><br>
      <span class="small">/mq</span><br>
      <span class="small">Encl.</span>
    </div>

    <div class="footer-bar" aria-hidden="true"></div>
  </main>
</body>
</html>
```